Building company buisness cards

We are looking for a sharp modern new look for our business cards.
We are a New Zealand based company that specialises in house and land packages.
We have attached a photo of the current logo and would like to see if it can be improved somehow if needed.
We are open to any colours but we have chosen green at this stage.
Feel free to change the font and make the logo smarter looking.
Play with the colours and see what looks best.

We want a card that looks so good know one will want to throw it away!

Target Market(s)

Home buyers

Industry/Entity Type

Building

Contact Information for Business Card

Derek Tolvane
0217394062
dtolvane@quillmarkhomesteads.co.nz
quillmarkhomesteads.co.nz

Font styles to use
Serif
Sans Serif

Colors

Designer to choose colors to be used in the design.

Requirements
Must have
• Logo and company name on one side, details on the other side
Nice to have
• Color codes for the original green are HEX #4a8028, RGB(74,128,40), CMYK(42,0,69,50)
• Round corners, Raised and/or spot UV

```html
<!DOCTYPE html>
<html lang="en">
<head>
<meta charset="utf-8">
<title>Quillmark Homesteads – Business Cards</title>
<link rel="stylesheet" href="https://fonts.googleapis.com/css2?family=Open+Sans:wght@400;700;800&display=swap">
<style>
  :root {
    --brand-green: #4a8028;
    --band-black: #1b1b1b;
    --card-white: #ffffff;
    --backdrop: #e7e4e2;
    --text-light: #ffffff;
  }
  * { margin: 0; padding: 0; box-sizing: border-box; }
  html, body {
    width: 1200px; height: 997px; overflow: hidden;
    background: var(--backdrop);
    font-family: "Open Sans", Arial, sans-serif;
  }
  .canvas {
    position: relative; width: 1200px; height: 997px;
  }
  .card {
    position: absolute; left: 260px;
    width: 680px; height: 388px;
    background: var(--card-white);
    border-radius: 6px;
    overflow: hidden;
    box-shadow: 0 2px 6px rgba(0,0,0,0.12);
  }
  .card--details { top: 80px; }
  .card--brand { top: 529px; }

  .wordmark {
    color: var(--brand-green);
    font-weight: 800;
    letter-spacing: -0.5px;
    line-height: 1;
    text-transform: lowercase;
  }
  .card--details .wordmark {
    position: absolute; left: 56px; top: 52px;
    font-size: 30px;
  }
  .card--brand .wordmark {
    position: absolute; left: 0; right: 0; top: 50%;
    transform: translateY(-50%);
    text-align: center;
    font-size: 46px;
  }

  .contact-band {
    position: absolute; left: 350px; right: 0; top: 112px; height: 92px;
    background: var(--band-black);
    color: var(--text-light);
    font-size: 15px; line-height: 26px;
    padding: 7px 0 0 18px;
  }
  .icon-column {
    position: absolute; left: 300px; top: 132px; width: 50px; height: 72px;
    background: var(--brand-green);
    display: flex; flex-direction: column; align-items: center;
    padding-top: 2px;
  }
  .icon-column svg { width: 14px; height: 14px; margin: 5px 0 7px; }
  .name-band {
    position: absolute; left: 0; top: 204px; width: 350px; height: 70px;
    background: var(--brand-green);
    color: var(--text-light);
    padding: 12px 0 0 56px;
  }
  .name-band .person-name { font-weight: 700; font-size: 19px; line-height: 24px; }
  .name-band .person-role { font-size: 15px; line-height: 22px; }
</style>
</head>
<body>
<main class="canvas">
  <section class="card card--details" aria-label="Business card, details side">
    <div class="wordmark">quillmark homesteads.</div>

    <div class="icon-column" aria-hidden="true">
      <svg viewBox="0 0 16 16"><path fill="#fff" d="M3 1.5l3 .5 1 3.5-1.8 1.2a9 9 0 0 0 4.1 4.1L10.5 9l3.5 1 .5 3-1.7 1.6C7 14.5 1.5 9 1.4 3.2z"/></svg>
      <svg viewBox="0 0 16 16"><rect x="1.5" y="3.5" width="13" height="9" rx="1" fill="none" stroke="#fff" stroke-width="1.6"/><path d="M2 4.5l6 4.5 6-4.5" fill="none" stroke="#fff" stroke-width="1.6"/></svg>
      <svg viewBox="0 0 16 16"><circle cx="8" cy="8" r="6.5" fill="none" stroke="#fff" stroke-width="1.4"/><ellipse cx="8" cy="8" rx="2.8" ry="6.5" fill="none" stroke="#fff" stroke-width="1.2"/><path d="M1.5 8h13M2.5 5h11M2.5 11h11" stroke="#fff" stroke-width="1.1"/></svg>
    </div>

    <div class="contact-band">
      <div class="contact-phone">0217394062</div>
      <div class="contact-email">dtolvane@quillmarkhomesteads.co.nz</div>
      <div class="contact-web">www.quillmarkhomesteads.co.nz</div>
    </div>

    <div class="name-band">
      <div class="person-name">Derek Tolvane</div>
      <div class="person-role">President</div>
    </div>
  </section>

  <section class="card card--brand" aria-label="Business card, brand side">
    <div class="wordmark">quillmark homesteads.</div>
  </section>
</main>
</body>
</html>
```